Veltrano.co - Polar Expeditions Specialists

We need a modern, visually striking business card for Veltrano.co, a company specialized in selling expedition cruises to the most remote regions on Earth, with a focus on the Arctic and Antarctica. The design should instantly communicate that the cardholder is an expert in polar travel. Use clean, premium aesthetics with cool tones like icy blue and white, possibly incorporating polar imagery (ice, glaciers, penguins, etc.)

Attached the logo

Contact Information for Business Card

Feels high-end and trustworthy.. Visually memorable — encourages people to keep it

Colors
0054AA
0677BA
7BADD7
CADEEF
E8F1F8

Requirements
Must have
• ice, glaciers, penguins, montains
Nice to have
• modern, transparente,

```html
<!DOCTYPE html>
<html lang="en">
<head>
<meta charset="utf-8">
<title>Veltrano.co Business Card</title>
<link href="https://fonts.googleapis.com/css2?family=Arimo:wght@400;700&family=Poppins:wght@600;700&display=swap" rel="stylesheet">
<style>
  :root {
    --brand-blue: #2f6cad;
    --ink: #1f1f1f;
    --ink-soft: #444444;
    --band-gray: #5a5a5a;
    --card-white: #f4f4f5;
    --backdrop: #e2e2e2;
  }
  * { margin: 0; padding: 0; box-sizing: border-box; }
  html, body { width: 1200px; height: 1040px; overflow: hidden; background: var(--backdrop); }
  .canvas { position: relative; width: 1200px; height: 1040px; }
  .card {
    position: absolute; left: 280px; width: 640px; height: 366px;
    border-radius: 20px; overflow: hidden;
    box-shadow: 0 3px 8px rgba(0,0,0,0.18);
  }
  .card-front { top: 130px; background: var(--card-white); }
  .card-back { top: 568px; background: var(--brand-blue); }

  .brand { position: absolute; left: 0; width: 100%; text-align: center; }
  .brand-mark { display: block; margin: 0 auto; border-radius: 50%; }
  .brand-name { font-family: "Poppins", sans-serif; font-weight: 700; line-height: 1; letter-spacing: -0.5px; }
  .brand-tagline { font-family: "Poppins", sans-serif; font-weight: 600; line-height: 1; }

  .card-front .brand { left: 386px; width: 240px; top: 38px; }
  .card-front .brand-mark { width: 44px; height: 44px; background: var(--brand-blue); }
  .card-front .brand-name { color: var(--brand-blue); font-size: 36px; margin-top: 24px; }
  .card-front .brand-tagline { color: var(--brand-blue); font-size: 11.5px; margin-top: 6px; }

  .holder { position: absolute; left: 45px; top: 204px; font-family: "Arimo", sans-serif; }
  .holder-name { color: var(--brand-blue); font-weight: 700; font-size: 26px; line-height: 1; }
  .holder-title { color: var(--ink-soft); font-size: 17px; margin-top: 4px; line-height: 1; }
  .divider { position: absolute; left: 45px; top: 255px; width: 554px; height: 1px; background: var(--ink); }

  .contact { position: absolute; top: 267px; font-family: "Arimo", sans-serif; font-size: 16.5px; color: var(--ink); line-height: 20px; }
  .contact-left { left: 45px; }
  .contact-left li { list-style: none; display: flex; align-items: center; gap: 8px; }
  .contact-left svg { width: 13px; height: 13px; fill: var(--brand-blue); }
  .contact-right { right: 41px; text-align: right; top: 268px; }

  .bands { position: absolute; left: 0; top: 0; width: 640px; height: 366px; }
  .website {
    position: absolute; right: 40px; top: 335px; color: #fff;
    font-family: "Arimo", sans-serif; font-size: 15px; letter-spacing: 1.6px; line-height: 1;
  }

  .card-back .brand { top: 90px; }
  .card-back .brand-mark { width: 60px; height: 60px; background: #ffffff; }
  .card-back .brand-name { color: #fff; font-size: 50px; margin-top: 38px; }
  .card-back .brand-tagline { color: #fff; font-size: 16px; margin-top: 8px; }
</style>
</head>
<body>
<div class="canvas">
  <section class="card card-front">
    <svg class="bands" viewBox="0 0 640 366" aria-hidden="true">
      <polygon points="0,337 348,337 335,350 0,350" fill="var(--band-gray)"/>
      <polygon points="373,326 640,326 640,366 0,366 0,354 344,354" fill="var(--brand-blue)"/>
    </svg>
    <div class="brand">
      <span class="brand-mark"></span>
      <div class="brand-name">Veltrano.co</div>
      <div class="brand-tagline">Polar Expeditions Specialists</div>
    </div>
    <div class="holder">
      <div class="holder-name">Nora Halvorsen</div>
      <div class="holder-title">President</div>
    </div>
    <div class="divider"></div>
    <ul class="contact contact-left">
      <li><svg viewBox="0 0 24 24"><path d="M6.6 10.8a15 15 0 0 0 6.6 6.6l2.2-2.2a1 1 0 0 1 1-.25 11.4 11.4 0 0 0 3.6.57 1 1 0 0 1 1 1V20a1 1 0 0 1-1 1A17 17 0 0 1 3 4a1 1 0 0 1 1-1h3.5a1 1 0 0 1 1 1c0 1.25.2 2.45.57 3.6a1 1 0 0 1-.25 1z"/></svg>(555) 2190-4476</li>
      <li><svg viewBox="0 0 24 24"><path d="M2 5h20v14H2z M3.5 6.5l8.5 6.5 8.5-6.5v1.6L12 14.6 3.5 8.1z" fill-rule="evenodd"/></svg>name@veltrano.com</li>
    </ul>
    <div class="contact contact-right">
      <div>2716 Harborview Lane</div>
      <div>Cedar Falls, NY 12034</div>
    </div>
    <div class="website">www.veltrano.com</div>
  </section>

  <section class="card card-back">
    <div class="brand">
      <span class="brand-mark"></span>
      <div class="brand-name">Veltrano.co</div>
      <div class="brand-tagline">Polar Expeditions Specialists</div>
    </div>
  </section>
</div>
</body>
</html>
```